My name is Delia Okonkwo,I want to create a web page for my personal dog grooming business. The name on the web page can be "Delia's Dog Grooming" I am located in San Antonio Texas. The page would help grow my customer base. Before and after pictures would display the quality of work that I do. On my page I can provide information about myself, my services, and pricing.
Updates

I have updated project to guaranteed pay

Please try to incorporate a schnauzer in an icon or logo. My dog is a schnauzer. THANKS!!!!!!!!!!!!

Target Market(s)

Dog Owners

Industry/Entity Type

Business

Requirements
Must have
• -A spot for before and after pictures.
-An about me section
-A section to make an appointment
Nice to have
• My favorite Color is purple. I think different shades of purple would be nice or purple with a light green

please incorporate a schnauzer in any icon or logo. My dog is a schnauzer.

```html
<!DOCTYPE html>
<html lang="en">
<head>
<meta charset="utf-8">
<title>Delia's Dog Grooming</title>
<link rel="stylesheet" href="https://fonts.googleapis.com/css2?family=Lobster&family=Cookie&family=Fredoka:wght@500;600&family=Arimo:wght@400&display=swap">
<style>
  :root {
    --plum-deep: #3a0036;
    --plum: #5c0a57;
    --plum-mid: #7a0e73;
    --magenta: #b417a8;
    --pink: #d965b3;
    --pink-edge: #c0399a;
    --button: #e2187c;
    --ink: #333333;
    --grey-light: #efefef;
    --grey-dark: #cdcdcd;
    --white: #ffffff;
    --photo-dark: #4a4440;
    --photo-mid: #8a8580;
  }
  * { margin: 0; padding: 0; box-sizing: border-box; }
  html, body { width: 1135px; height: 1200px; overflow: hidden; }
  body {
    position: relative;
    background: linear-gradient(#f4f3f6 0, #ffffff 520px);
    font-family: "Arimo", Arial, sans-serif;
    color: var(--ink);
    border-top: 4px solid var(--plum-deep);
  }
  .abs { position: absolute; }

  /* navigation */
  .nav { position: absolute; top: -4px; left: 0; width: 1135px; height: 49px; font-size: 15px; }
  .nav a { position: absolute; color: #1a1a1a; text-decoration: none; white-space: nowrap; }
  .nav .current {
    left: 649px; top: 0;
    background: linear-gradient(var(--plum-mid), var(--plum-deep));
    color: var(--white); width: 94px; height: 49px; border-radius: 0 0 8px 8px;
    display: flex; align-items: center; justify-content: center; padding-top: 4px;
  }
  .nav .link { top: 17px; }

  /* brand */
  .brand-mark { left: 72px; top: 40px; width: 78px; height: 78px; border-radius: 50%; background: var(--plum-mid); }
  .brand-name { left: 170px; top: 38px; font-family: "Lobster", cursive; font-size: 40px; line-height: 50px; color: var(--plum); white-space: nowrap; }

  .photo { background: radial-gradient(ellipse at 50% 45%, var(--photo-mid), var(--photo-dark) 70%, rgba(74,68,64,0.15) 100%); }
  .hero-photo { left: 735px; top: 97px; width: 360px; height: 400px; border-radius: 45% 40% 20% 20%; background: radial-gradient(ellipse at 50% 40%, #6f6a66, #2e2b2a 55%, #c9c6c4 85%, rgba(255,255,255,0) 100%); }

  /* slider */
  .slider { left: 66px; top: 177px; width: 667px; height: 318px; border: 4px solid var(--plum-deep); border-radius: 9px; overflow: hidden; background: var(--white); }
  .slider svg { position: absolute; left: 0; top: 0; }
  .slider-photo { left: 2px; top: 25px; width: 270px; height: 250px; border-radius: 40%; }
  .slider-title { left: 330px; top: 72px; font-family: "Lobster", cursive; font-size: 46px; font-weight: 400; color: var(--white); }
  .slider-text { left: 336px; top: 145px; font-family: "Cookie", cursive; font-size: 22px; line-height: 26px; color: var(--white); white-space: nowrap; }
  .dots { left: 584px; top: 286px; display: flex; gap: 3px; }
  .dots span { width: 11px; height: 11px; border-radius: 50%; background: var(--plum); }
  .dots .on { background: #dddddd; width: 13px; height: 13px; margin-top: -1px; }

  /* about */
  .heading { font-family: "Lobster", cursive; font-size: 30px; font-weight: 400; color: var(--plum); letter-spacing: -0.5px; }
  .about-title { left: 71px; top: 542px; }
  .about-text { left: 71px; top: 592px; font-size: 12.3px; line-height: 26px; white-space: nowrap; }

  .appointment { left: 755px; top: 538px; width: 326px; height: 179px; border: 2px solid var(--pink-edge); border-radius: 7px; background: linear-gradient(var(--pink) 0, var(--pink) 88%, #cf4fa6 88%); }
  .appointment-text { left: 26px; top: 22px; width: 160px; text-align: center; font-family: "Fredoka", sans-serif; font-weight: 600; font-size: 24px; line-height: 32px; color: var(--white); }
  .appointment-button { left: 42px; top: 130px; width: 129px; height: 31px; border-radius: 9px; border: 2px solid #f7a0c8; background: linear-gradient(#f04a97, var(--button) 55%, #b80f62); color: var(--white); font-family: "Fredoka", sans-serif; font-weight: 600; font-size: 18px; text-align: center; line-height: 27px; }
  .appointment-dog { left: 965px; top: 562px; width: 110px; height: 190px; border-radius: 40% 40% 30% 30%; background: linear-gradient(#9d9a9a, #6c6a6a); }

  /* grey band */
  .band { left: 0; top: 768px; width: 1135px; height: 257px; border-top: 2px solid #d6d6d6; background: linear-gradient(var(--grey-light), var(--grey-dark)); }
  .grooming-title { left: 69px; top: 788px; }
  .before-photo { left: 70px; top: 857px; width: 209px; height: 140px; border-radius: 8px; }
  .after-photo { left: 472px; top: 859px; width: 209px; height: 140px; border-radius: 8px; }
  .arrow { position: absolute; }
  .services-title { left: 763px; top: 788px; }
  .service-list { list-style: none; top: 844px; }
  .service-list li { height: 23.8px; font-size: 15px; color: #3a3a3a; display: flex; align-items: center; white-space: nowrap; }
  .service-list li::before { content: ""; width: 11px; height: 11px; border-radius: 50%; background: var(--plum); margin-right: 14px; }
  .services-divider { left: 909px; top: 845px; width: 2px; height: 126px; background: #a9a9a9; }

  /* footer */
  .footer { left: 0; top: 1025px; width: 1135px; height: 175px; background: linear-gradient(var(--plum-deep), var(--plum) 100%); color: var(--white); font-size: 15px; }
  .footer-links { left: 75px; top: 32px; white-space: nowrap; }
  .footer-copy { left: 75px; top: 64px; white-space: nowrap; }
  .connect { left: 837px; top: 32px; white-space: nowrap; }
  .social { left: 837px; top: 78px; display: flex; gap: 9px; }
  .social span { width: 39px; height: 39px; border-radius: 50%; background: var(--white); }
</style>
</head>
<body>

<nav class="nav">
  <a class="current" href="#">Home</a>
  <a class="link" href="#" style="left:766px">About us</a>
  <a class="link" href="#" style="left:844px">Gallery</a>
  <a class="link" href="#" style="left:922px">Services</a>
  <a class="link" href="#" style="left:1000px">Contact Us</a>
</nav>

<div class="abs brand-mark" aria-hidden="true"></div>
<div class="abs brand-name">Delia's<br>Dog Grooming</div>

<div class="abs hero-photo" role="img" aria-label="Photo of a schnauzer puppy lying down"></div>

<section class="abs slider">
  <svg width="667" height="318" viewBox="0 0 667 318" aria-hidden="true">
    <defs>
      <radialGradient id="slideGlow" cx="0.28" cy="0.65" r="0.75">
        <stop offset="0" stop-color="#c11bb4"/>
        <stop offset="0.55" stop-color="#7a0a72"/>
        <stop offset="1" stop-color="#3e0039"/>
      </radialGradient>
    </defs>
    <path d="M215 0 C 320 60, 320 230, 235 318 L 667 318 L 667 0 Z" fill="url(#slideGlow)"/>
  </svg>
  <div class="abs photo slider-photo" role="img" aria-label="Photo of a schnauzer puppy"></div>
  <h1 class="abs slider-title">Welcome</h1>
  <p class="abs slider-text">The standard chunk of Lorem Ipsum used<br>since the 1500s is reproduced below for<br>those interested.</p>
  <div class="abs dots"><span></span><span class="on"></span><span></span></div>
</section>

<h2 class="abs heading about-title">About Me</h2>
<p class="abs about-text">Lorem Ipsum is simply dummy text of the printing and typesetting industry. Lorem Ipsum has been the industry's<br>standard dummy text ever since the 1500s, when an unknown printer took a galley of type and scrambled it to make a<br>type specimen book. It has survived not only five centuries, but also the leap into electronic typesetting, remaining<br>essentially unchanged. It was popularised in the 1960s with the release of Lexaform sheets containing Lorem Ipsum<br>passages, and more recently with desktop publishing software like Orvel PageSmith including versions of Lorem Ipsum.</p>

<section class="abs appointment">
  <div class="abs appointment-text">Make<br>An<br>Apointment</div>
  <div class="abs appointment-button">Click Here</div>
</section>
<div class="abs appointment-dog" role="img" aria-label="Illustration of a grey schnauzer"></div>

<section class="abs band"></section>
<h2 class="abs heading grooming-title">Our Grooming</h2>
<div class="abs photo before-photo" role="img" aria-label="Before photo of a schnauzer prior to grooming"></div>
<div class="abs photo after-photo" role="img" aria-label="After photo of a freshly groomed schnauzer"></div>

<svg class="arrow" style="left:248px;top:836px" width="128" height="112" viewBox="0 0 128 112" aria-hidden="true">
  <path d="M8 60 L62 8 L62 30 L118 30 L118 72 L62 72 L62 96 Z" fill="#c8283a" transform="translate(0,10)"/>
  <path d="M8 60 L62 8 L62 30 L118 30 L118 72 L62 72 L62 96 Z" fill="#111111"/>
  <text x="70" y="58" fill="#ffffff" font-family="Arimo, sans-serif" font-size="20" text-anchor="middle" transform="rotate(-28 70 58)">Before</text>
</svg>
<svg class="arrow" style="left:394px;top:836px" width="128" height="112" viewBox="0 0 128 112" aria-hidden="true">
  <path d="M120 60 L66 8 L66 30 L10 30 L10 72 L66 72 L66 96 Z" fill="#c8283a" transform="translate(0,10)"/>
  <path d="M120 60 L66 8 L66 30 L10 30 L10 72 L66 72 L66 96 Z" fill="#111111"/>
  <text x="56" y="58" fill="#ffffff" font-family="Arimo, sans-serif" font-size="20" text-anchor="middle" transform="rotate(28 56 58)">After</text>
</svg>

<h2 class="abs heading services-title">Our Services</h2>
<ul class="abs service-list" style="left:763px"><li>Lorem Ipsum</li><li>Lorem Ipsum</li><li>Lorem Ipsum</li><li>Lorem Ipsum</li><li>Lorem Ipsum</li></ul>
<div class="abs services-divider"></div>
<ul class="abs service-list" style="left:948px"><li>Lorem Ipsum</li><li>Lorem Ipsum</li><li>Lorem Ipsum</li><li>Lorem Ipsum</li><li>Lorem Ipsum</li></ul>

<footer class="abs footer">
  <div class="abs footer-links">Home &nbsp;| &nbsp;About us &nbsp;&nbsp;| &nbsp;Gallery &nbsp;| &nbsp;Services &nbsp;| Contact Us</div>
  <div class="abs footer-copy">Copyright@2011 www.deliasgrooming.com</div>
  <div class="abs connect">Connect With Us</div>
  <div class="abs social" aria-label="Social links">
    <span></span><span></span><span></span><span></span><span></span>
  </div>
</footer>

</body>
</html>
```